Business Cards for new orthopaedic surgery practice

My husband and I are starting our own orthopaedic surgery practice. We are looking for a business card that is uniform, but one will have my name/title and the other will have his. You can just create one design with my name on it for now. But when I choose your design as the winning design I will ask that you add another copy with his name/title.

We are looking for classy, simple, elite all in one. We like dark blues/a little gold/yellow. Something that goes with our logo. We want our logo incorporated. Here is all the info you need:
Business name: RV Bone & Vitality Center
Location: 38517 North Willowmere Ave
Maple Hollow, FL 33990
Phone: 954-218-4063
Fax: 954-582-7341
Email: info@myrvbonecare.example

Names: Lydia Vance, M.D.
Board Certified Hand and Upper Extremity Surgeon

Ebo Dansu, M.D.
Board Certified Hip & Knee Replacement/General Orthopaedic Surgeon

Can decide what you want to put on the back. Maybe a slogan:
Grounded in Healing. Centered on You

I am just going to upload our logo. The only thing is if we select you as the winning design, the location, and phone numbers may change. We will need your help to update that once fully solidified.

Industry/Entity Type

Medical

Contact Information for Business Card

Colors
0054AA
0677BA
7BADD7
CADEEF
E8F1F8
0094D4
00A9DD
6FCCEA
C7EBF8
E9F6FB

Requirements
Must have
• class, appeal,
Should not have
• We want to air on the side of masculine if we are looking at masculine vs. feminine feel. But we still want it classy, sophisticated, and something we will love

```html
<!DOCTYPE html>
<html lang="en">
<head>
<meta charset="utf-8">
<title>RV Bone &amp; Vitality Center – Business Cards</title>
<link href="https://fonts.googleapis.com/css2?family=Libre+Baskerville:wght@400;700&display=swap" rel="stylesheet">
<style>
  :root {
    --stage: #2b2b2d;
    --navy: #1c2a52;
    --navy-soft: #2c3d6e;
    --gold: #c8a766;
    --white: #ffffff;
    --ink: #1c2a52;
  }
  * { box-sizing: border-box; margin: 0; padding: 0; }
  html, body { width: 1200px; height: 694px; overflow: hidden; }
  body {
    background: var(--stage);
    font-family: "Libre Baskerville", "Times New Roman", serif;
    position: relative;
  }
  .card {
    position: absolute;
    top: 192px;
    width: 540px;
    height: 310px;
    border-radius: 20px;
    overflow: hidden;
  }
  .card--back { left: 40px; background: var(--navy); }
  .card--front { left: 620px; background: var(--white); }
  .card__shapes { position: absolute; inset: 0; }

  .brand-mark {
    position: absolute;
    display: flex;
    align-items: center;
    justify-content: center;
    text-align: center;
    border-radius: 50%;
    font-weight: 400;
    letter-spacing: 0.12em;
    text-transform: uppercase;
    line-height: 1.5;
  }
  .card--back .brand-mark {
    left: 190px; top: 40px; width: 160px; height: 160px;
    border: 1.5px solid var(--navy-soft);
    color: var(--navy-soft);
    font-size: 13px;
  }
  .slogan {
    position: absolute;
    left: 0; right: 0; top: 232px;
    text-align: center;
    color: var(--white);
    font-size: 19px;
    letter-spacing: 0.02em;
  }

  .card--front .brand-mark--primary {
    left: 45px; top: 40px; width: 150px; height: 150px;
    border: 1.5px solid var(--gold);
    color: var(--ink);
    font-size: 12px;
    font-weight: 700;
  }
  .card--front .brand-mark--secondary {
    left: 395px; top: 118px; width: 110px; height: 110px;
    border: 1.5px solid var(--white);
    color: var(--white);
    font-size: 9px;
    font-weight: 700;
  }
  .identity {
    position: absolute;
    right: 26px; top: 26px;
    text-align: right;
    color: var(--ink);
  }
  .identity__name { font-size: 23px; font-weight: 700; margin-bottom: 6px; }
  .identity__title { font-size: 13px; line-height: 1.4; }

  .contact {
    position: absolute;
    left: 34px; top: 224px;
    list-style: none;
    color: var(--white);
    font-size: 12px;
    line-height: 1.5;
  }
  .contact__item { display: flex; align-items: flex-start; gap: 10px; margin-bottom: 2px; }
  .contact__icon { width: 13px; height: 13px; flex: none; margin-top: 2px; }
</style>
</head>
<body>

<section class="card card--back" aria-label="Card back">
  <div class="brand-mark">RV Bone &amp;<br>Vitality<br>Center</div>
  <p class="slogan">Grounded in Healing. Centered on You</p>
</section>

<section class="card card--front" aria-label="Card front">
  <svg class="card__shapes" width="540" height="310" viewBox="0 0 540 310" aria-hidden="true">
    <polygon points="0,222 540,92 540,310 0,310" fill="var(--navy)"/>
    <polygon points="330,144 540,92 540,236" fill="var(--gold)"/>
    <line x1="0" y1="214" x2="540" y2="84" stroke="var(--gold)" stroke-width="2"/>
  </svg>

  <div class="brand-mark brand-mark--primary">RV Bone &amp;<br>Vitality<br>Center</div>

  <div class="identity">
    <h1 class="identity__name">Lydia Vance, M.D.</h1>
    <p class="identity__title">Board Certified Hand and<br>Upper Extremity Surgeon</p>
  </div>

  <div class="brand-mark brand-mark--secondary">RV Bone &amp;<br>Vitality<br>Center</div>

  <ul class="contact">
    <li class="contact__item">
      <svg class="contact__icon" viewBox="0 0 24 24" aria-label="Phone"><path fill="var(--gold)" d="M6.6 10.8a15.1 15.1 0 0 0 6.6 6.6l2.2-2.2a1 1 0 0 1 1-.25 11.4 11.4 0 0 0 3.6.57 1 1 0 0 1 1 1V20a1 1 0 0 1-1 1A17 17 0 0 1 3 4a1 1 0 0 1 1-1h3.5a1 1 0 0 1 1 1c0 1.250.2 2.450.57 3.57a1 1 0 0 1-.25 1z"/></svg>
      <span>954-218-4063</span>
    </li>
    <li class="contact__item">
      <svg class="contact__icon" viewBox="0 0 24 24" aria-label="Fax"><path fill="var(--gold)" d="M6 2h9l3 3v5H6zM3 11h18v11H3zm4 3v2h3v-2zm5 0v2h3v-2zm-5 4v2h3v-2zm5 0v2h3v-2z"/></svg>
      <span>954-582-7341</span>
    </li>
    <li class="contact__item">
      <svg class="contact__icon" viewBox="0 0 24 24" aria-label="Address"><path fill="var(--gold)" d="M12 2a7 7 0 0 0-7 7c0 5.2 7 13 7 13s7-7.8 7-13a7 7 0 0 0-7-7zm0 9.5A2.5 2.5 0 1 1 12 6.5a2.5 2.5 0 0 1 0 5z"/></svg>
      <span>38517 North Willowmere Ave<br>Maple Hollow, FL 33990</span>
    </li>
  </ul>
</section>

</body>
</html>
```